Real estate business card

I need a business card for my real estate company. I help clients buy and sell properties. I would like to keep the design very simple and professional. I would like the design to convey professionalism, safety and trust. I prefer no graphics but a simple logo design would be nice if that is part of what you do.
Updates

Please keep the designs simple. No high-rise buildings please. 

Project Deadline Extended
Reason: My design has not been finalized.

Target Market(s)

Age group 30-60 mostly affluent

Industry/Entity Type

Real Estate

Contact Information for Business Card

Velmont Realtors
Gregory Velmont, Broker
4815 Brindle Ave. #263, La Crescenta, CA 91206

Requirements
Nice to have
• Logo can be combination of my initials GV or just Z or a simple geometric shape? Please see "Desig Ideas" attachment. No pics of houses or shaking hands, dollar bills, $, %, etc...
Please use fonts similar to Helvetica for a clean, modern look (think Northern European design, simple, clean yet bold)

Also use font colors such as blue, grey in different shades. Use pastel colors if better.

```html
<!DOCTYPE html>
<html lang="en">
<head>
<meta charset="utf-8">
<title>Velmont Realtors – Business Card</title>
<link rel="stylesheet" href="https://fonts.googleapis.com/css2?family=Open+Sans:wght@400;600;700&display=swap">
<style>
  :root {
    --page-bg: #e9e7e3;
    --card-white: #ffffff;
    --panel-dark: #333333;
    --band-grey: #8d8f93;
    --accent-blue: #4f86c6;
    --wash-blue: #c9d8ea;
    --wash-light: #eef4f8;
    --text-dark: #3a3a3a;
    --text-light: #ffffff;
    --icon-grey: #9a9a9a;
  }
  * { margin: 0; padding: 0; box-sizing: border-box; }
  html, body { width: 1200px; height: 1020px; overflow: hidden; }
  body {
    background: var(--page-bg);
    font-family: "Open Sans", Helvetica, Arial, sans-serif;
    position: relative;
  }
  .business-card {
    position: absolute;
    left: 100px; top: 224px;
    width: 1000px; height: 572px;
    background: var(--card-white);
    overflow: hidden;
    box-shadow: 0 10px 30px rgba(0,0,0,0.18);
  }
  .name-panel {
    position: absolute; left: 0; top: 0;
    width: 580px; height: 400px;
    background: var(--panel-dark);
    border-bottom: 8px solid var(--band-grey);
  }
  .side-wash {
    position: absolute; right: 0; top: 0;
    width: 90px; height: 572px;
    background: linear-gradient(180deg, var(--wash-light), var(--wash-blue));
  }
  .holder {
    position: absolute; left: 48px; top: 300px;
    color: var(--text-light);
  }
  .holder-name { font-size: 38px; font-weight: 700; letter-spacing: 1px; line-height: 1.1; }
  .holder-title { font-size: 20px; font-weight: 400; letter-spacing: 1.5px; margin-top: 4px; }
  .brand {
    position: absolute; left: 580px; width: 330px; top: 180px;
    display: flex; align-items: center; justify-content: center; gap: 12px;
  }
  .brand-dot { width: 16px; height: 16px; border-radius: 50%; background: var(--accent-blue); flex: none; }
  .brand-name {
    font-size: 24px; font-weight: 600; letter-spacing: 2px;
    color: var(--text-dark); text-transform: uppercase; white-space: nowrap;
  }
  .contact-list {
    position: absolute; left: 48px; top: 432px;
    list-style: none;
  }
  .contact-item {
    display: flex; align-items: center; gap: 16px;
    height: 30px; font-size: 16px; color: var(--text-dark);
  }
  .contact-icon {
    width: 34px; height: 22px; background: var(--icon-grey);
    display: flex; align-items: center; justify-content: center;
  }
</style>
</head>
<body>
  <div class="business-card">
    <div class="name-panel"></div>
    <div class="side-wash" role="img" aria-label="Soft pale blue background wash"></div>

    <div class="holder">
      <div class="holder-name">MARTIN ELLERY</div>
      <div class="holder-title">GENERAL MANAGER</div>
    </div>

    <div class="brand">
      <span class="brand-dot"></span>
      <span class="brand-name">Velmont Realtors</span>
    </div>

    <ul class="contact-list">
      <li class="contact-item">
        <span class="contact-icon"><svg width="12" height="12" viewBox="0 0 12 12"><path d="M2 1 L4 1 L5 4 L3.5 5 Q5 8 7 8.5 L8 7 L11 8 L11 10 Q6 12 2 6 Q0.5 3 2 1Z" fill="#fff"/></svg></span>
        <span>014 275 3906</span>
      </li>
      <li class="contact-item">
        <span class="contact-icon"><svg width="14" height="10" viewBox="0 0 14 10"><rect x="0.5" y="0.5" width="13" height="9" fill="none" stroke="#fff"/><path d="M0.5 0.5 L7 5.5 L13.5 0.5" fill="none" stroke="#fff"/></svg></span>
        <span>martin@velmontmail.com</span>
      </li>
      <li class="contact-item">
        <span class="contact-icon"><svg width="12" height="12" viewBox="0 0 12 12"><circle cx="6" cy="6" r="5" fill="none" stroke="#fff"/><path d="M1 6 H11 M6 1 Q3 6 6 11 Q9 6 6 1" fill="none" stroke="#fff"/></svg></span>
        <span>www.velmontrealty.com</span>
      </li>
      <li class="contact-item">
        <span class="contact-icon"><svg width="10" height="13" viewBox="0 0 10 13"><path d="M5 12 Q0 6 0 5 A5 5 0 0 1 10 5 Q10 6 5 12Z" fill="#fff"/><circle cx="5" cy="5" r="1.8" fill="#9a9a9a"/></svg></span>
        <span>412, 9th floor, Brindle Ave Tower LCR</span>
      </li>
    </ul>
  </div>
</body>
</html>
```